Designer Instructions – Updated Referral Program Flyer

(Based on the mock-up in “Brief Layout and Instructions.pdf”)

OVERALL STYLE + LAYOUT

Maintain the same general layout, structure, and flow as the mock-up flyer (front and back).

This is an update of an older flyer, not a full redesign — keep the same sections, proportions, and overall visual feel, but with cleaner, more modern design improvements.

The final flyer should look clean, bold, professional, and high-impact, geared toward realtors, property managers, and contractors who refer work.

FRONT SIDE INSTRUCTIONS
1. Header Section

Remove the Rebuild Harbor Crest logo from the top banner.
(Shown on page 1 of the PDF)

2. Main Headline

Keep the same three-line structure:
EARN
UNLIMITED
CASH

Center it, maximize impact, and increase the font size of CASH so all three words match in importance.

Make the headline bold, clean, and the main focal point.

3. Cash Incentive Box

Keep the "$500 minimum OR 10% per referral" box, but upgrade the graphics to look sharper and more modern.

Ensure the wording matches exactly what’s in the mock-up.

4. Premier Partner Program Ribbon

Clean up and modernize the "PREMIER PARTNER PROGRAM" bar while keeping the same position and structure.

Ensure the checkmark badge remains crisp and professional.

5. Supporting Icons Section

Keep the four icons/benefit boxes (Guaranteed Payout, Free Evaluations, Affordable Solutions, Industry Leaders) in the same order.

Update the icons to cleaner, more modern styles — but maintain the same meanings.

Improve alignment and spacing for sharper visual consistency.

6. Remove Icons in Contact Area

At the bottom (“CALL TEXT OR BOOK ONLINE 858-471-6093 BrightlaneRenovate.com”), remove the phone and internet icons, as noted on page 2 of the PDF.

7. Replace All Images

I (Dorian) will provide all updated stock images separately via email.

Replace the flood/water-damage imagery and roof leak with the new images I send.

Keep image placement and proportions the same as the mock-up.

BACK SIDE INSTRUCTIONS
1. Header Image + “REFER / EARN” Section

Maintain the same large split-image layout (“The more you refer, the more you earn”).

Replace all background imagery with the new assets I will send.

Keep the CASH FLOW image section but modernize the type and spacing.

2. “HOW IT WORKS” Section

Preserve the three-column layout:

Refer Flood, Water & Mold Damage

We Take Care of Everything (evaluations/insurance)

Get Paid to Share

Update images, tighten spacing, and use modern iconography.

3. Remove Phone/Internet Icons

Same as the front side — remove small communication icons and keep only the text/number/URL.

4. Bottom Contact Bar

Keep the blue bar, same wording, same layout — just modernize the style if needed for clarity.

5. Replace All Back-Side Images

Again, I will email you the image assets.

Keep the layout EXACT — just update with higher-quality photos and improved design.

TEXT CONTENT (Keep as-is unless spacing adjustments needed)

All text shown in the PDF should remain exactly the same unless spacing or visual balance requires minor adjustments.
Example from page 3:

“REFER FLOOD, MOLD & CONSTRUCTION JOBS”

“We Schedule a Free Estimate. If Approved, You Get Paid.”

“Everybody Benefits From Referrals”

Everything stays, just refreshed and visually improved.

DESIGN GOALS

Flyer should look high-end and trustworthy, not salesy.

Consistent color theme: blues, whites, yellows, same palette as original.

Use bold, modern fonts with strong readability.

Ensure all headlines pop and all benefit boxes are clean, well-aligned, and evenly spaced.

The final result should feel like a premium referral program flyer for a top-tier restoration/remodel company.

FILES I WILL PROVIDE

I will send the designer:

All replacement stock photos

Any updated logos (if needed)

Original high-resolution version of the mock-up (if available)

Any additional icons preferred

Colors
0054AA
0677BA
7BADD7
CADEEF
E8F1F8

Requirements
Must have
• Designer Instructions – Updated Referral Program Flyer (Based on the mock-up in “Brief Layout and Instructions.pdf”) OVERALL STYLE + LAYOUT Maintain the same general layout, structure, and flow as the mock-up flyer (front and back). This is an update of an older flyer, not a full redesign — keep the same sections, proportions, and overall visual feel, but with cleaner, more modern design improvements. The final flyer should look clean, bold, professional, and high-impact, geared toward realtors, property managers, and contractors who refer work. FRONT SIDE INSTRUCTIONS 1. Header Section Remove the Rebuild Harbor Crest logo from the top banner. (Shown on page 1 of the PDF) 2. Main Headline Keep the same three-line structure: EARN UNLIMITED CASH Center it, maximize impact, and increase the font size of CASH so all three words match in importance. Make the headline bold, clean, and the main focal point. 3. Cash Incentive Box Keep the "$500 minimum OR 10% per referral" box, but upgrade the graphics to look sharper and more modern. Ensure the wording matches exactly what’s in the mock-up. 4. Premier Partner Program Ribbon Clean up and modernize the "PREMIER PARTNER PROGRAM" bar while keeping the same position and structure. Ensure the checkmark badge remains crisp and professional. 5. Supporting Icons Section Keep the four icons/benefit boxes (Guaranteed Payout, Free Evaluations, Affordable Solutions, Industry Leaders) in the same order. Update the icons to cleaner, more modern styles — but maintain the same meanings. Improve alignment and spacing for sharper visual consistency. 6. Remove Icons in Contact Area At the bottom (“CALL TEXT OR BOOK ONLINE 858-471-6093 BrightlaneRenovate.com”), remove the phone and internet icons, as noted on page 2 of the PDF. 7. Replace All Images I (Dorian) will provide all updated stock images separately via email. Replace the flood/water-damage imagery and roof leak with the new images I send. Keep image placement and proportions the same as the mock-up. BACK SIDE INSTRUCTIONS 1. Header Image + “REFER / EARN” Section Maintain the same large split-image layout (“The more you refer, the more you earn”). Replace all background imagery with the new assets I will send. Keep the CASH FLOW image section but modernize the type and spacing. 2. “HOW IT WORKS” Section Preserve the three-column layout: Refer Flood, Water & Mold Damage We Take Care of Everything (evaluations/insurance) Get Paid to Share Update images, tighten spacing, and use modern iconography. 3. Remove Phone/Internet Icons Same as the front side — remove small communication icons and keep only the text/number/URL. 4. Bottom Contact Bar Keep the blue bar, same wording, same layout — just modernize the style if needed for clarity. 5. Replace All Back-Side Images Again, I will email you the image assets. Keep the layout EXACT — just update with higher-quality photos and improved design. TEXT CONTENT (Keep as-is unless spacing adjustments needed) All text shown in the PDF should remain exactly the same unless spacing or visual balance requires minor adjustments. Example from page 3: “REFER FLOOD, MOLD & CONSTRUCTION JOBS” “We Schedule a Free Estimate. If Approved, You Get Paid.” “Everybody Benefits From Referrals” Everything stays, just refreshed and visually improved. DESIGN GOALS Flyer should look high-end and trustworthy, not salesy. Consistent color theme: blues, whites, yellows, same palette as original. Use bold, modern fonts with strong readability. Ensure all headlines pop and all benefit boxes are clean, well-aligned, and evenly spaced. The final result should feel like a premium referral program flyer for a top-tier restoration/remodel company. FILES I WILL PROVIDE I will send the designer: All replacement stock photos Any updated logos (if needed) Original high-resolution version of the mock-up (if available) Any additional icons preferred

```html
<!DOCTYPE html>
<html lang="en">
<head>
<meta charset="utf-8">
<title>Referral Program Flyer – Front and Back</title>
<link rel="stylesheet" href="https://fonts.googleapis.com/css2?family=Anton&family=Montserrat:wght@500;600;700;800;900&family=Oswald:wght@500;600;700&display=swap">
<style>
  :root{
    --navy:#13306b;
    --navy-deep:#0f2a5e;
    --blue:#1f4fa0;
    --brand-blue:#0054AA;
    --mid-blue:#0677BA;
    --sky:#7BADD7;
    --pale:#CADEEF;
    --mist:#E8F1F8;
    --yellow:#f7dc12;
    --orange:#f7941d;
    --red:#d8262f;
    --ink:#1a1a1a;
    --stage-dark:#636266;
    --stage-light:#c9c8cb;
    --paper:#ffffff;
    --paper-cool:#f2f4f7;
  }
  *{margin:0;padding:0;box-sizing:border-box}
  html,body{width:1200px;height:2374px;overflow:hidden}
  body{
    position:relative;
    background:linear-gradient(to bottom,var(--stage-dark) 0,var(--stage-dark) 1518px,var(--stage-light) 1518px);
    font-family:"Montserrat",Arial,sans-serif;
    color:var(--navy);
  }
  .card{
    position:absolute;left:152px;width:896px;height:580px;overflow:hidden;
    box-shadow:0 14px 22px rgba(0,0,0,.35);
  }
  .card--front{top:130px;background:var(--paper)}
  .card--back{top:841px;height:579px;background:var(--paper-cool)}
  .card svg.shapes{position:absolute;inset:0;width:100%;height:100%}
  .abs{position:absolute;white-space:nowrap}

  /* FRONT */
  .headline{left:30px;top:40px;font-weight:900;line-height:1}
  .headline__top{font-size:45px;letter-spacing:.3px;color:var(--blue)}
  .headline__cash{font-size:84px;margin-top:6px;color:var(--navy);letter-spacing:-1px}

  .incentive{left:44px;top:215px;width:366px;height:52px;background:var(--blue);box-shadow:8px 8px 10px rgba(0,0,0,.18)}
  .incentive__amount{position:absolute;left:24px;top:3px;color:#fff;font-weight:800;font-size:30px;line-height:1}
  .incentive__min{position:absolute;left:38px;top:35px;color:var(--yellow);font-weight:800;font-size:11px}
  .incentive__or{position:absolute;left:118px;top:-7px;width:66px;height:66px;border-radius:50%;background:var(--yellow);border:4px solid #fff;
    font-family:"Oswald",sans-serif;font-weight:600;font-size:32px;color:var(--navy);display:flex;align-items:center;justify-content:center}
  .incentive__pct{position:absolute;left:194px;top:0;font-family:"Oswald",sans-serif;font-weight:500;font-size:40px;color:var(--sky);line-height:1.2}
  .incentive__per{position:absolute;left:270px;top:10px;color:var(--yellow);font-weight:800;font-size:12.5px;line-height:1.25}

  .benefit__title{font-weight:800;font-size:13px;line-height:1.3;color:var(--blue);text-transform:uppercase}
  .benefit__text{font-weight:500;font-size:11px;line-height:1.4;color:var(--ink);margin-top:9px}
  .benefit__icon{position:absolute;width:32px;height:32px;border-radius:50%;border:2px solid var(--yellow);background:#fff;display:flex;align-items:center;justify-content:center}
  .benefit__icon svg{width:18px;height:18px}

  .flood-title{left:590px;top:22px;width:306px;text-align:center;font-weight:800;font-size:24px;line-height:1.35;color:var(--yellow)}
  .partner-cta{left:596px;top:398px;width:300px;text-align:center;font-weight:800;font-size:26px;line-height:1.32;color:var(--yellow)}

  .ribbon{left:483px;top:207px;width:242px}
  .ribbon__top{height:18px;background:var(--yellow);text-align:center;font-weight:800;font-size:11px;line-height:18px;color:var(--blue)}
  .ribbon__main{height:35px;background:var(--blue);display:flex;justify-content:space-between;align-items:center;padding:0 8px;
    font-family:"Oswald",sans-serif;font-weight:500;font-size:21px;color:var(--yellow)}
  .ribbon__check{position:absolute;left:97px;top:16px;width:48px;height:48px;border-radius:50%;background:var(--yellow);border:3px solid #fff;display:flex;align-items:center;justify-content:center}

  .contact-strip{left:0;top:538px;height:42px;display:flex;align-items:center;padding-left:50px;gap:6px;color:var(--navy)}
  .contact-strip__label{font-weight:500;font-size:16px}
  .contact-strip__phone{font-weight:800;font-size:27px}
  .contact-strip__url{left:612px;top:538px;width:284px;height:42px;display:flex;align-items:center;justify-content:center;font-weight:800;font-size:16px;color:var(--navy)}

  /* BACK */
  .step__photo{position:absolute;width:104px;height:104px;border-radius:50%;border:3px solid var(--navy);overflow:hidden}
  .step__box{position:absolute;background:var(--yellow);border:2px solid var(--navy);border-left:none;border-radius:0 8px 8px 0;padding:12px 6px 10px 60px}
  .step__title{font-weight:800;font-size:11.5px;line-height:1.4;color:var(--blue);white-space:nowrap}
  .step__text{font-weight:500;font-size:10.5px;line-height:1.4;color:var(--ink);margin-top:5px;white-space:nowrap}

  .back-contact{left:37px;top:459px;color:var(--navy)}
  .back-contact__label{font-weight:500;font-size:16px}
  .back-contact__phone{font-weight:800;font-size:29px;margin-top:2px}
  .back-contact__url{font-weight:800;font-size:18px;margin-top:8px}

  .slogan{left:524px;top:46px;width:210px;font-family:"Anton",sans-serif;line-height:1;text-transform:uppercase}
  .slogan__small{font-size:36px;color:#fff;letter-spacing:.3px}
  .slogan__big{font-size:88px;background:linear-gradient(to bottom,var(--yellow) 35%,var(--orange));-webkit-background-clip:text;background-clip:text;color:transparent;margin:0}

  .badge-24{left:404px;top:430px;width:126px;height:126px;border-radius:50%;background:#fff;border:4px solid var(--red);display:flex;flex-direction:column;align-items:center;justify-content:center}
  .badge-24__num{font-family:"Anton",sans-serif;font-size:52px;line-height:1;color:var(--red)}
  .badge-24__word{font-weight:800;font-size:14px;color:var(--red);margin-top:-2px}
</style>
</head>
<body>

<!-- FRONT SIDE -->
<section class="card card--front" aria-label="Referral flyer front">
  <svg class="shapes" viewBox="0 0 896 580" aria-hidden="true">
    <polygon points="612,0 896,0 896,130 560,130" fill="#13306b"/>
    <polygon points="580,0 612,0 540,205 508,205" fill="#f7dc12"/>
    <line x1="700" y1="100" x2="896" y2="100" stroke="#1f4fa0" stroke-width="1"/>
    <polygon points="535,140 560,140 382,538 357,538" fill="#13306b"/>
    <polygon points="0,538 600,538 580,580 0,580" fill="#8fb7de"/>
    <polygon points="612,538 896,538 896,580 590,580" fill="#f7dc12"/>
    <polygon points="600,538 624,538 602,580 580,580" fill="#13306b"/>
  </svg>

  <div class="abs" role="img" aria-label="Photo of a flooded dining room interior with water on the floor"
       style="left:0;top:0;width:896px;height:538px;clip-path:polygon(560px 130px,896px 130px,896px 538px,382px 538px);background:linear-gradient(160deg,#e6e7e5 0%,#b7ada0 45%,#6d5a48 100%)"></div>
  <div class="abs" style="left:0;top:0;width:896px;height:538px;clip-path:polygon(650px 330px,896px 330px,896px 538px,555px 538px);background:rgba(19,48,107,.86)"></div>

  <div class="abs headline">
    <div class="headline__top">EARN UNLIMITED</div>
    <div class="headline__cash">CASH</div>
  </div>

  <div class="abs incentive">
    <span class="incentive__amount">$500</span>
    <span class="incentive__min">MINIMUM</span>
    <span class="incentive__or">OR</span>
    <span class="incentive__pct">10%</span>
    <span class="incentive__per">PER<br>REFERRAL</span>
  </div>

  <div class="abs benefit" style="left:22px;top:320px">
    <div class="benefit__title">Guaranteed<br>Payout*</div>
    <div class="benefit__text">Minimum $500 or 10% of<br>Total Invoice Paid Fast</div>
    <span class="benefit__icon" style="left:110px;top:-2px"><svg viewBox="0 0 24 24" fill="none" stroke="#13306b" stroke-width="2"><circle cx="12" cy="12" r="8"/><path d="M8 12l3 3 5-6"/></svg></span>
  </div>
  <div class="abs benefit" style="left:208px;top:320px">
    <div class="benefit__title">Free Estimates</div>
    <div class="benefit__text">Fast &amp; Free Inspections<br>&amp; Written Estimates</div>
    <span class="benefit__icon" style="left:142px;top:-2px"><svg viewBox="0 0 24 24" fill="none" stroke="#13306b" stroke-width="2"><rect x="5" y="3" width="12" height="17" rx="1"/><path d="M8 8h6M8 12h6M8 16h4"/></svg></span>
  </div>
  <div class="abs benefit" style="left:22px;top:425px">
    <div class="benefit__title">Affordable<br>Solutions</div>
    <div class="benefit__text">Lowest Out of Pocket<br>Costs for Your Customers</div>
    <span class="benefit__icon" style="left:116px;top:-2px"><svg viewBox="0 0 24 24" fill="none" stroke="#13306b" stroke-width="2"><circle cx="12" cy="9" r="5"/><path d="M4 18c3 0 5 2 8 2s5-2 8-2"/></svg></span>
  </div>
  <div class="abs benefit" style="left:208px;top:425px">
    <div class="benefit__title">Industry<br>Leaders</div>
    <div class="benefit__text">Licensed &amp; Certified<br>Experts&nbsp; Provide 100%<br>Guarantee</div>
    <span class="benefit__icon" style="left:102px;top:-2px"><svg viewBox="0 0 24 24" fill="none" stroke="#13306b" stroke-width="2"><circle cx="12" cy="7" r="3"/><circle cx="6" cy="13" r="2.5"/><circle cx="18" cy="13" r="2.5"/><path d="M3 20h18"/></svg></span>
  </div>

  <div class="abs flood-title">GET PAID TOREFER<br>A FLOOD</div>

  <div class="abs ribbon">
    <div class="ribbon__top">PREMIER</div>
    <div class="ribbon__main"><span>PARTNER</span><span>PROGRAM</span></div>
    <span class="ribbon__check"><svg width="26" height="26" viewBox="0 0 24 24" fill="none" stroke="#13306b" stroke-width="4" stroke-linecap="round" stroke-linejoin="round"><path d="M4 12l5 5 11-11"/></svg></span>
  </div>

  <div class="abs partner-cta">PARTNER WITH<br>US &amp; EVERYBODY<br>WINS!</div>

  <div class="abs contact-strip">
    <span class="contact-strip__label">CALL TEXT OR BOOK ONLINE</span>
    <span class="contact-strip__phone">858-471-6093</span>
  </div>
  <div class="abs contact-strip__url">BRIGHTLANERENOVATE.COM</div>
</section>

<!-- BACK SIDE -->
<section class="card card--back" aria-label="Referral flyer back">
  <svg class="shapes" viewBox="0 0 896 579" aria-hidden="true">
    <polygon points="896,100 896,579 640,579" fill="#dfe3e8"/>
    <polygon points="868,150 896,120 662,579 630,579" fill="#1f4fa0"/>
    <polygon points="836,150 870,150 680,494 645,494" fill="#c3c6cc"/>
  </svg>

  <div class="abs" role="img" aria-label="Photo of a bright modern living room with white sofa"
       style="left:0;top:0;width:896px;height:579px;clip-path:polygon(896px 130px,896px 579px,664px 579px);background:linear-gradient(150deg,#f4f5f6,#cfd3d7 60%,#a9adb2)"></div>

  <div class="abs" role="img" aria-label="Photo of dollar bills with faint letters, tinted navy"
       style="left:0;top:0;width:896px;height:579px;clip-path:polygon(530px 0,884px 0,704px 491px,290px 491px);background:linear-gradient(160deg,#1c3a78,#13306b 55%,#0f2a5e)"></div>

  <div class="abs step__box" style="left:88px;top:37px;width:226px;height:90px">
    <div class="step__title">REFER FLOOD, MOLD &amp;<br>CONSTRUCTION JOBS:</div>
    <div class="step__text">It's Simple to Refer 24/7:<br>Call, Text or Book Online.</div>
  </div>
  <div class="step__photo" role="img" aria-label="Photo of a technician inspecting a ceiling" style="left:31px;top:30px;background:linear-gradient(135deg,#d9d2c8,#6b6f78)"></div>

  <div class="abs step__box" style="left:88px;top:181px;width:241px;height:91px">
    <div class="step__title">WE TAKE CARE OF<br>EVERYTHING:</div>
    <div class="step__text">We Schedule a Free Estimate.<br>If Approved, You Get Paid.</div>
  </div>
  <div class="step__photo" role="img" aria-label="Photo of a house with an estimate form on a clipboard" style="left:31px;top:175px;background:linear-gradient(135deg,#b9c7d6,#6d7f58)"></div>

  <div class="abs step__box" style="left:88px;top:326px;width:226px;height:91px">
    <div class="step__title">Everybody Benefits<br>From Referrals</div>
    <div class="step__text">We Provide Expert Quality<br>Work for AAordable Price.</div>
  </div>
  <div class="step__photo" role="img" aria-label="Illustration of a yellow road sign reading get paid to share" style="left:31px;top:320px;background:linear-gradient(135deg,#a9cfee,#f7dc12)"></div>

  <div class="abs back-contact">
    <div class="back-contact__label">CALL TEXT OR BOOK ONLINE</div>
    <div class="back-contact__phone">858-471-6093</div>
    <div class="back-contact__url">BRIGHTLANERENOVATE.COM</div>
  </div>

  <div class="abs slogan">
    <div class="slogan__small">The more you</div>
    <div class="slogan__big">Refer</div>
    <div class="slogan__small">The more you</div>
    <div class="slogan__big" style="font-size:104px">Earn</div>
  </div>

  <div class="abs badge-24">
    <span class="badge-24__num">24</span>
    <span class="badge-24__word">HOUR</span>
  </div>
</section>

</body>
</html>
```